High-end construction company needs a business card design

We need a modern looking business card that draws people in, is memorable and looks so good people will want to sick it on their fridges.
On the first side what is needed are:
Logo
My name - Tomasz Brelwik
Title - Managing Director
Website - www.varkelt.co.uk
Email - tomasz@varkelt.co.uk
Telephone - 020 5194 6281
Mobile - 07845139072
On the back side was is needed is a list of all the services we provide:
-Kitchen Renovations
-Bathroom Renovations
-House Renovations
-Garage Conversions
-Extensions
-Loft Conversions
-Conservatories
-Carpentry
-Tiling
-Electrical
-Plumbing & Heating
-Bricklaying
-Landscaping
-Decorating
-Plastering
We would like the colours to be the same shades as on the logo with grey or black for the words.
Target Market(s)
Anyone who needs building work done
Contact Information for Business Card
This business card is for a construction company which strives to deliver excellent service and quality.
The look and feel of the card should represent this.
Requirements
Must have
- On the first side what is needed are:
Logo
My name - Tomasz Brelwik
Title - Managing Director
Website - www.varkelt.co.uk
Email - tomasz@varkelt.co.uk
Telephone - 020 5194 6281
Mobile - 07845139072
Nice to have
- Cool looking features

```html
<!DOCTYPE html>
<html lang="en">
<head>
<meta charset="utf-8">
<title>Varkelt Construction Ltd – Business Card</title>
<link href="https://fonts.googleapis.com/css2?family=Arimo:wght@400;700&display=swap" rel="stylesheet">
<style>
  :root {
    --backdrop: #2a2a2a;
    --card-white: #ffffff;
    --brand-green: #74bd43;
    --deep-green: #3f9a2f;
    --text-white: #ffffff;
    --divider: rgba(255,255,255,0.55);
  }
  * { box-sizing: border-box; margin: 0; padding: 0; }
  html, body {
    width: 1200px; height: 900px; overflow: hidden;
    background: var(--backdrop);
    font-family: "Arimo", Arial, sans-serif;
  }
  .canvas {
    width: 1200px; height: 900px;
    display: flex; align-items: center; justify-content: center; gap: 40px;
  }
  .card {
    width: 560px; height: 362px; position: relative;
    box-shadow: 0 14px 30px rgba(0,0,0,0.55);
  }

  /* Services side */
  .card--services { background: var(--card-white); color: var(--deep-green); padding: 48px 30px 0 34px; }
  .brand { display: flex; align-items: center; gap: 10px; justify-content: center; }
  .brand__mark { width: 22px; height: 22px; background: currentColor; }
  .brand__name { font-weight: 700; font-size: 30px; letter-spacing: 1px; text-transform: uppercase; line-height: 1.05; }
  .brand__name small { display: block; font-size: 13px; letter-spacing: 3px; }
  .card--services .brand { color: var(--deep-green); margin-bottom: 40px; }
  .services { display: flex; justify-content: space-between; }
  .services ul { list-style: none; }
  .services li { font-size: 14.5px; line-height: 1.45; position: relative; padding-left: 13px; }
  .services li::before {
    content: ""; position: absolute; left: 0; top: 7px;
    width: 6px; height: 6px; border-radius: 50%; background: var(--brand-green);
  }

  /* Contact side */
  .card--contact { background: var(--brand-green); color: var(--text-white); display: flex; align-items: center; }
  .card--contact .brand { width: 270px; flex-direction: column; gap: 10px; color: var(--text-white); }
  .card--contact .brand__name { text-align: center; font-size: 34px; }
  .card--contact .brand__name small { font-size: 14px; }
  .contact-divider { width: 1px; height: 190px; background: var(--divider); margin-right: 28px; }
  .person__name { font-weight: 700; font-size: 19px; text-transform: uppercase; letter-spacing: 0.5px; }
  .person__title { font-size: 14px; margin-bottom: 26px; }
  .contacts { list-style: none; }
  .contacts li { display: flex; align-items: center; gap: 8px; font-size: 14px; line-height: 1.55; }
  .contacts svg { width: 13px; height: 13px; flex: none; }
</style>
</head>
<body>
<main class="canvas">

  <section class="card card--services">
    <div class="brand">
      <span class="brand__mark"></span>
      <div class="brand__name">Varkelt<small>Construction Ltd</small></div>
    </div>
    <div class="services">
      <ul>
        <li>Kitchen Renovations</li>
        <li>Bathroom Renovations</li>
        <li>House Renovations</li>
        <li>Garage Conversions</li>
        <li>Extensions</li>
      </ul>
      <ul>
        <li>Loft Conversions</li>
        <li>Conservatories</li>
        <li>Carpentry</li>
        <li>Tiling</li>
        <li>Electrical</li>
      </ul>
      <ul>
        <li>Plumbing &amp; Heating</li>
        <li>Bricklaying</li>
        <li>Landscaping</li>
        <li>Decorating</li>
        <li>Plastering</li>
      </ul>
    </div>
  </section>

  <section class="card card--contact">
    <div class="brand">
      <span class="brand__mark"></span>
      <div class="brand__name">Varkelt<small>Construction Ltd</small></div>
    </div>
    <div class="contact-divider"></div>
    <div class="person">
      <h1 class="person__name">Tomasz Brelwik</h1>
      <p class="person__title">Managing Director</p>
      <ul class="contacts">
        <li>
          <svg viewBox="0 0 24 24" fill="currentColor" aria-hidden="true"><path d="M6.6 10.8a15.1 15.1 0 0 0 6.6 6.6l2.2-2.2c.3-.3.7-.4 1-.2 1.1.4 2.3.6 3.6.6.6 0 1 .4 1 1V20c0 .6-.4 1-1 1A17 17 0 0 1 3 4c0-.6.4-1 1-1h3.5c.6 0 1 .4 1 1 0 1.3.2 2.5.6 3.6.1.3 0 .7-.2 1z"/></svg>
          020 5194 6281
        </li>
        <li>
          <svg viewBox="0 0 24 24" fill="none" stroke="currentColor" stroke-width="2" aria-hidden="true"><rect x="6" y="2" width="12" height="20" rx="2"/><line x1="11" y1="18" x2="13" y2="18"/></svg>
          07845139072
        </li>
        <li>
          <svg viewBox="0 0 24 24" fill="none" stroke="currentColor" stroke-width="2" aria-hidden="true"><rect x="2" y="5" width="20" height="14"/><path d="M2 5l10 8 10-8"/></svg>
          tomasz@varkelt.co.uk
        </li>
        <li>
          <svg viewBox="0 0 24 24" fill="none" stroke="currentColor" stroke-width="2" aria-hidden="true"><circle cx="12" cy="12" r="10"/><path d="M2 12h20M12 2c3 3 3 17 0 20M12 2c-3 3-3 17 0 20"/></svg>
          www.varkelt.co.uk
        </li>
      </ul>
    </div>
  </section>

</main>
</body>
</html>
```